Business Card for my New Brokerage

Looking to get a business card design for my new Real Estate Brokerage.
I want it with Picture, Phone Number, Email, Website, Office Address
Name and Designation. Please add logo too.

Target Market(s)

Real Estate Investors or Home Buyers

Industry/Entity Type

Real Estate

Contact Information for Business Card

Name, Email, Phone Number, website, email, office address

Colors
EB3D1F
EC4F4E
F09395
F8D3D4
FCEDEE

Requirements
Must have
• Minimalistic, Clean, Modern, Photo
Nice to have
• White and Red Colors

```html
<!DOCTYPE html>
<html lang="en">
<head>
<meta charset="utf-8">
<title>Ember Realty Inc – Business Card</title>
<link href="https://fonts.googleapis.com/css2?family=Montserrat:wght@700&family=Fira+Sans:wght@800&family=Roboto:wght@400&display=swap" rel="stylesheet">
<style>
  :root {
    --backdrop: #232323;
    --card-white: #ffffff;
    --brand-red: #dd0000;
    --gold: #c4944a;
    --gold-light: #f3dc8f;
    --gold-dark: #b98a43;
    --photo-dark: #3a3a3a;
    --text-light: #ffffff;
  }
  * { box-sizing: border-box; margin: 0; padding: 0; }
  html, body { width: 1075px; height: 1200px; overflow: hidden; }
  body { background: var(--backdrop); position: relative; font-family: "Roboto", Arial, sans-serif; }

  .card {
    position: absolute; left: 206px; width: 663px; height: 395px;
    overflow: hidden; box-shadow: 3px 3px 4px rgba(0,0,0,.55);
  }
  .card--front { top: 187px; background: var(--card-white); }
  .card--back { top: 637px; background: var(--brand-red); }

  .wordmark { position: absolute; font-family: "Montserrat", sans-serif; font-weight: 700; line-height: 1; text-align: center; }
  .wordmark__name { display: block; font-size: 78px; letter-spacing: -1px; }
  .wordmark__sub { display: block; font-size: 22px; letter-spacing: 5px; margin-top: 6px; }
  .card--front .wordmark { left: 35px; top: 95px; width: 302px; color: var(--brand-red); }
  .card--back .wordmark { left: 40px; top: 65px; width: 260px; color: var(--text-light); }
  .card--back .wordmark__name { font-size: 68px; }
  .card--back .wordmark__sub { font-size: 20px; margin-top: 4px; }

  .portrait {
    position: absolute; left: 325px; top: 0; width: 338px; height: 395px;
    background: linear-gradient(180deg, var(--card-white) 0%, var(--card-white) 52%, var(--photo-dark) 66%, #2a2a2a 100%);
  }
  .gold-rule { position: absolute; left: 0; top: 260px; width: 323px; height: 9px; background: var(--gold); }
  .name-band { position: absolute; left: 0; top: 269px; width: 330px; height: 126px; background: var(--brand-red); }
  .person-name { position: absolute; left: 35px; top: 35px; font-family: "Fira Sans", sans-serif; font-weight: 800; font-size: 27px; color: var(--text-light); letter-spacing: .3px; white-space: nowrap; }
  .person-role { position: absolute; left: 35px; top: 68px; font-size: 19px; color: var(--text-light); white-space: nowrap; }

  .contact { position: absolute; left: 39px; top: 204px; color: var(--text-light); font-size: 19px; list-style: none; }
  .contact li { display: flex; align-items: center; height: 23.5px; white-space: nowrap; }
  .contact svg { width: 16px; height: 16px; margin-right: 7px; fill: none; stroke: var(--text-light); stroke-width: 1.8; }
  .address { position: absolute; left: 35px; top: 298px; color: var(--text-light); font-size: 19px; line-height: 23.5px; font-style: normal; white-space: nowrap; }

  .gold-panel {
    position: absolute; left: 468px; top: 0; width: 195px; height: 395px;
    background: linear-gradient(110deg, var(--gold-dark) 0%, var(--gold-light) 55%, var(--gold-dark) 100%);
  }
</style>
</head>
<body>
  <section class="card card--front">
    <div class="portrait" role="img" aria-label="Portrait photo of the agent in a dark suit and tie on a white background"></div>
    <div class="wordmark">
      <span class="wordmark__name">EMBER</span>
      <span class="wordmark__sub">REALTY INC</span>
    </div>
    <div class="gold-rule"></div>
    <div class="name-band">
      <h1 class="person-name">MARCUS REED</h1>
      <p class="person-role">Managing Director</p>
    </div>
  </section>

  <section class="card card--back">
    <div class="wordmark">
      <span class="wordmark__name">EMBER</span>
      <span class="wordmark__sub">REALTY INC</span>
    </div>
    <ul class="contact">
      <li><svg viewBox="0 0 16 16"><path d="M3 2l3 3-1.5 2a8 8 0 0 0 4.5 4.5L11 10l3 3-2 2C6 14 2 10 1 4z"/></svg>044-318 627 905</li>
      <li><svg viewBox="0 0 16 16"><rect x="1" y="3.5" width="14" height="9"/><path d="M1 3.5l7 5 7-5"/></svg>info@emberhq.com</li>
      <li><svg viewBox="0 0 16 16"><circle cx="8" cy="8" r="6.5"/><ellipse cx="8" cy="8" rx="3" ry="6.5"/><path d="M1.5 8h13M2.5 5h11M2.5 11h11"/></svg>www.emberrealty.net</li>
    </ul>
    <address class="address">738, Harbor Lane, Suite 12<br>60317,Northland</address>
    <div class="gold-panel"></div>
  </section>
</body>
</html>
```